KV HOLDING Business Cards

I need business cards for "KV Holding group LLC" doublesided... logo on the back (also include logo on front)
logo attached to project... i have jpg up..
Company Info:
827 North Cadwell Avenue, Suite 4B
Chicago, Illinois 60654
facsimile 312-481-2075 (list fax, address, website on all cards.)
www.kvholdinggroup.example
Three different people on cards:
Darnell P. Okafor, CPA MST
Principal
ofc 312-481-3900
mobile 312-204-7751
darnellpokafor@kvholdinggroup.example
Hollis T. Brennecke, CPA MST
Principal
hollistbrennecke@kvholdinggroup.example
mobile 708-539-1184
ofc 312-481-3900
Conrad M Pavlik
Principal
ofc 312-481-3900
no mobile
conradmpavlik@kvholdinggroup.example
I have multiple projects listed.. see below:
Business cards for amber gate ventures llc
letterhead
envelopes
Business cards for KV Holding LLC
letterhead
envelopes
Target Market(s)
rich people
Industry/Entity Type
Business
Look and feel
Each slider illustrates characteristics of the customer's brand and the style your logo design should communicate.

```html
<!DOCTYPE html>
<html lang="en">
<head>
<meta charset="utf-8">
<title>KV Holding Group LLC — Business Cards</title>
<link rel="stylesheet" href="https://fonts.googleapis.com/css2?family=Roboto:wght@400&display=swap">
<style>
  :root {
    --backdrop: #3a3a3a;
    --card-back: #c4c4c4;
    --card-front: #ffffff;
    --navy: #173f72;
    --white: #ffffff;
    --text-font: "Roboto", Arial, sans-serif;
  }
  * { margin: 0; padding: 0; box-sizing: border-box; }
  html, body { width: 1200px; height: 1000px; overflow: hidden; }
  body { background: var(--backdrop); font-family: var(--text-font); position: relative; }

  .card { position: absolute; width: 500px; overflow: hidden; }
  .card-back { left: 77px; background: var(--card-back); height: 292px; }
  .card-front { left: 631px; background: var(--card-front); height: 292px; }
  .row-1 { top: 31px; }
  .row-2 { top: 348px; }
  .row-3 { top: 668px; }

  /* back side */
  .brand-block {
    position: absolute; left: 0; right: 0; top: 120px;
    text-align: center; color: var(--navy);
  }
  .brand-name { font-size: 34px; letter-spacing: 1px; line-height: 1; }
  .brand-url { font-size: 21px; letter-spacing: 3px; margin-top: 14px; line-height: 1; }

  /* front side */
  .holder { position: absolute; left: 35px; color: var(--navy); }
  .holder-name { font-size: 22px; line-height: 1; }
  .holder-title { font-size: 13px; line-height: 1; margin-top: 3px; }
  .name-rule {
    position: absolute; left: 0; width: 283px; height: 3px; background: var(--navy);
  }
  .mini-brand {
    position: absolute; left: 299px; color: var(--navy);
    font-size: 16px; line-height: 1; white-space: nowrap;
  }
  .contacts { position: absolute; left: 35px; list-style: none; color: var(--navy); font-size: 11px; }
  .contacts-dense li { line-height: 14.5px; }
  .contacts-open li { line-height: 17px; }
  .address-band {
    position: absolute; left: 0; right: 0; bottom: 0; height: 43px;
    background: var(--navy); color: var(--white);
    font-size: 10px; padding-left: 35px; display: flex; align-items: center; white-space: nowrap;
  }
</style>
</head>
<body>

<!-- Card set 1 -->
<section class="card card-back row-1">
  <div class="brand-block">
    <p class="brand-name">KV Holding Group LLC</p>
    <p class="brand-url">www.kvholdinggroup.example</p>
  </div>
</section>
<section class="card card-front row-1">
  <div class="holder" style="top:77px">
    <p class="holder-name">Darnell P. Okafor, CPA MST</p>
    <p class="holder-title">Principal</p>
  </div>
  <div class="name-rule" style="top:117px"></div>
  <p class="mini-brand" style="top:120px">KV Holding Group LLC</p>
  <ul class="contacts contacts-dense" style="top:147px">
    <li>Office : 312-481-3900</li>
    <li>Direct : 312-481-3917</li>
    <li>Mobile : 312-204-7751</li>
    <li>Facsimile : 312-481-2075</li>
    <li>Email : darnellpokafor@kvholdinggroup.example</li>
  </ul>
  <p class="address-band">827 North Cadwell Avenue, Suite 4B Chicago, Illinois 60654 &nbsp;|&nbsp; www.kvholdinggroup.example</p>
</section>

<!-- Card set 2 -->
<section class="card card-back row-2">
  <div class="brand-block">
    <p class="brand-name">KV Holding Group LLC</p>
    <p class="brand-url">www.kvholdinggroup.example</p>
  </div>
</section>
<section class="card card-front row-2">
  <div class="holder" style="top:74px">
    <p class="holder-name">Hollis T. Brennecke, CPA MST</p>
    <p class="holder-title">Principal</p>
  </div>
  <div class="name-rule" style="top:116px"></div>
  <p class="mini-brand" style="top:119px">KV Holding Group LLC</p>
  <ul class="contacts contacts-open" style="top:147px">
    <li>Office : 312-481-3900</li>
    <li>Mobile : 708-539-1184</li>
    <li>Facsimile : 312-481-2075</li>
    <li>Email : hollistbrennecke@kvholdinggroup.example</li>
  </ul>
  <p class="address-band" style="height:45px">827 North Cadwell Avenue, Suite 4B Chicago, Illinois 60654 &nbsp;|&nbsp; www.kvholdinggroup.example</p>
</section>

<!-- Card set 3 -->
<section class="card card-back row-3">
  <div class="brand-block">
    <p class="brand-name">KV Holding Group LLC</p>
    <p class="brand-url">www.kvholdinggroup.example</p>
  </div>
</section>
<section class="card card-front row-3">
  <div class="holder" style="top:75px">
    <p class="holder-name">Conrad M Pavlik</p>
    <p class="holder-title">Principal</p>
  </div>
  <div class="name-rule" style="top:115px"></div>
  <p class="mini-brand" style="top:119px">KV Holding Group LLC</p>
  <ul class="contacts contacts-open" style="top:158px">
    <li>Office : 312-481-3900</li>
    <li>Facsimile : 312-481-2075</li>
    <li>Email : conradmpavlik@kvholdinggroup.example</li>
  </ul>
  <p class="address-band" style="height:47px">827 North Cadwell Avenue, Suite 4B Chicago, Illinois 60654 &nbsp;|&nbsp; www.kvholdinggroup.example</p>
</section>

</body>
</html>
```